I need a business card design for a new business based in South West Australia.
I specialize in residential window cleaning & general handyman maintenance.

Dale Marsh - 412 SILVER HAWK DETAILING
- Window Cleaning
- House Maintenance

```html
<!DOCTYPE html>
<html lang="en">
<head>
<meta charset="utf-8">
<title>412 Silver Hawk Detailing – Business Card</title>
<link rel="stylesheet" href="https://fonts.googleapis.com/css2?family=Roboto+Slab:wght@700&family=Arimo:wght@400&display=swap">
<style>
  :root {
    --backdrop: #e9e6e1;
    --card-white: #f7f8f9;
    --sky: #c6e3f0;
    --sky-soft: #e3f1f8;
    --ink: #141414;
    --panel: #fbfbfb;
  }
  html, body {
    margin: 0;
    width: 1200px;
    height: 892px;
    overflow: hidden;
    background: var(--backdrop);
  }
  .card {
    position: absolute;
    left: 100px;
    top: 160px;
    width: 1000px;
    height: 572px;
    background: var(--card-white);
    border-radius: 6px;
    box-shadow: 0 10px 30px rgba(0,0,0,0.18);
    overflow: hidden;
  }
  .card__art {
    position: absolute;
    inset: 0;
  }
  .card__title {
    position: absolute;
    left: 220px;
    top: 44px;
    margin: 0;
    font-family: "Roboto Slab", serif;
    font-weight: 700;
    font-size: 46px;
    line-height: 1;
    color: var(--ink);
    white-space: nowrap;
  }
  .card__illustration {
    position: absolute;
    left: 22px;
    top: 170px;
    width: 210px;
    height: 330px;
    border-radius: 60px;
    background: radial-gradient(ellipse at 50% 60%, #d7ecf6 0%, #bfe0ef 70%, rgba(198,227,240,0) 100%);
  }
  .info-panel {
    position: absolute;
    left: 330px;
    top: 215px;
    width: 620px;
    height: 305px;
    background: var(--panel);
    border-radius: 32px;
  }
  .info-panel__name {
    position: absolute;
    left: 48px;
    top: 56px;
    margin: 0;
    font-family: "Roboto Slab", serif;
    font-weight: 700;
    font-size: 52px;
    line-height: 1;
    color: var(--ink);
    white-space: nowrap;
  }
  .services {
    position: absolute;
    left: 60px;
    top: 160px;
    margin: 0;
    padding: 0;
    list-style: none;
  }
  .services__item {
    display: flex;
    align-items: center;
    gap: 22px;
    height: 58px;
    font-family: "Arimo", sans-serif;
    font-size: 32px;
    color: var(--ink);
  }
  .services__icon {
    width: 26px;
    height: 26px;
    flex: none;
  }
</style>
</head>
<body>
  <div class="card">
    <svg class="card__art" viewBox="0 0 1000 572" width="1000" height="572" aria-hidden="true">
      <defs>
        <linearGradient id="wipe" x1="0" y1="0" x2="1" y2="0">
          <stop offset="0" stop-color="#e3f1f8"/>
          <stop offset="0.35" stop-color="#c6e3f0"/>
          <stop offset="1" stop-color="#c6e3f0"/>
        </linearGradient>
      </defs>
      <path d="M175,140 Q560,60 1000,95 L1000,572 L175,572 Z" fill="url(#wipe)"/>
    </svg>

    <h1 class="card__title">412 Silver Hawk Detailing</h1>

    <div class="card__illustration" role="img" aria-label="Illustration of a window squeegee wiping through soap bubbles"></div>

    <section class="info-panel">
      <h2 class="info-panel__name">Dale Marsh</h2>
      <ul class="services">
        <li class="services__item">
          <svg class="services__icon" viewBox="0 0 26 26" aria-hidden="true">
            <path d="M5 13.5l5 5L21 7" fill="none" stroke="#5a9fc0" stroke-width="3" stroke-linecap="round" stroke-linejoin="round"/>
          </svg>
          Window Cleaning
        </li>
        <li class="services__item">
          <svg class="services__icon" viewBox="0 0 26 26" aria-hidden="true">
            <path d="M5 13.5l5 5L21 7" fill="none" stroke="#5a9fc0" stroke-width="3" stroke-linecap="round" stroke-linejoin="round"/>
          </svg>
          House Maintenance
        </li>
      </ul>
    </section>
  </div>
</body>
</html>
```